Business Card Design

I need business cards designed for a new company i have started that makes cakes, particularly themed kids cakes with a really modern design and I would like to have my business cards reflect this. I have attached some photos of cakes I have made and would like some to be used.

Industry/Entity Type

Business

Contact Information for Business Card

Business Name: Tarts and Treats by Maren
Mobile: 0492 815 063
email: maren@tartsandtreatsbymaren.example.au
Instagram: instagram.com/tartsandtreatsbymaren/
Facebook: fb.me/tartsandtreatsbymaren

Colors
e667a6
b768aa
3276b5

Requirements
Must have
• Business Name: Tarts and Treats by Maren
• Mobile: 0492 815 063
• email: maren@tartsandtreatsbymaren.example.au
• Instagram: instagram.com/tartsandtreatsbymaren/
• Facebook: fb.me/tartsandtreatsbymaren
Nice to have
• 2 to 3 pictures of my cakes

```html
<!DOCTYPE html>
<html lang="en">
<head>
<meta charset="utf-8">
<title>Tarts and Treats by Maren — Business Card</title>
<link href="https://fonts.googleapis.com/css2?family=Open+Sans:wght@400;600;700&display=swap" rel="stylesheet">
<style>
  :root {
    --pink: #e667a6;
    --purple: #b768aa;
    --blue: #3276b5;
    --blue-deep: #1f5c98;
    --ink: #4a4a4a;
    --rule: #d6d6d6;
    --paper: #ffffff;
    --stage: #ecebe8;
  }
  * { box-sizing: border-box; margin: 0; padding: 0; }
  html, body {
    width: 1200px; height: 843px; overflow: hidden;
    background: var(--stage);
    font-family: "Open Sans", Arial, sans-serif;
  }
  .stage {
    position: relative; width: 1200px; height: 843px;
  }
  .card {
    position: absolute; left: 300px; width: 600px; height: 343px;
    border-radius: 3px; overflow: hidden;
    box-shadow: 0 6px 18px rgba(0,0,0,.16);
  }
  .card--back {
    top: 55px;
    background: linear-gradient(135deg, #5a9ad3 0%, var(--blue) 50%, var(--blue-deep) 100%);
    display: flex; align-items: center; justify-content: center;
  }
  .card--front {
    top: 443px; background: var(--paper);
  }
  .wordmark {
    display: flex; align-items: center; gap: 14px;
    font-weight: 600; line-height: 1.1;
  }
  .wordmark__dot {
    width: 22px; height: 22px; border-radius: 50%; flex: none;
  }
  .wordmark__name { font-size: 30px; }
  .wordmark__by { font-size: 15px; letter-spacing: 4px; margin-top: 6px; }
  .card--back .wordmark { color: #fff; }
  .card--back .wordmark__dot { background: #fff; }
  .card--front .wordmark {
    position: absolute; left: 34px; top: 108px; width: 230px;
    color: var(--pink);
  }
  .card--front .wordmark__dot { background: var(--pink); }
  .card--front .wordmark__name { font-size: 25px; }
  .card--front .wordmark__by { font-size: 13px; }
  .divider {
    position: absolute; left: 284px; top: 78px; width: 1px; height: 150px;
    background: var(--rule);
  }
  .contact {
    position: absolute; left: 306px; top: 86px; right: 16px; color: var(--ink);
  }
  .contact__name {
    color: var(--pink); font-weight: 700; font-size: 19px; letter-spacing: .5px;
  }
  .contact__role { font-size: 13px; margin-bottom: 14px; }
  .contact__list { list-style: none; }
  .contact__item {
    display: flex; align-items: center; gap: 9px;
    font-size: 12.5px; line-height: 1; margin-bottom: 8px; white-space: nowrap;
  }
  .contact__icon {
    width: 14px; height: 14px; flex: none;
    fill: none; stroke: var(--ink); stroke-width: 1.6;
  }
  .contact__square {
    width: 12px; height: 12px; margin: 0 1px; background: var(--ink); border-radius: 2px; flex: none;
  }
  .band {
    position: absolute; left: 0; right: 0; bottom: 0; height: 30px; display: flex;
  }
  .band__seg { flex: 1; }
  .band__seg--pink { background: var(--pink); }
  .band__seg--blue { background: var(--blue); }
  .band__seg--purple { background: var(--purple); }
</style>
</head>
<body>
<main class="stage">
  <section class="card card--back" aria-label="Card back">
    <div class="wordmark">
      <span class="wordmark__dot"></span>
      <div>
        <div class="wordmark__name">Tarts and Treats</div>
        <div class="wordmark__by">BY MAREN</div>
      </div>
    </div>
  </section>

  <section class="card card--front" aria-label="Card front">
    <div class="wordmark">
      <span class="wordmark__dot"></span>
      <div>
        <div class="wordmark__name">Tarts and Treats</div>
        <div class="wordmark__by">BY MAREN</div>
      </div>
    </div>
    <div class="divider"></div>
    <div class="contact">
      <div class="contact__name">LEO HARTLEY</div>
      <div class="contact__role">CEO/Founder</div>
      <ul class="contact__list">
        <li class="contact__item">
          <svg class="contact__icon" viewBox="0 0 14 14"><rect x="3.5" y="1" width="7" height="12" rx="1.5"/><line x1="6" y1="11" x2="8" y2="11"/></svg>
          0492 815 063
        </li>
        <li class="contact__item">
          <svg class="contact__icon" viewBox="0 0 14 14"><rect x="1" y="3" width="12" height="8" rx="1"/><polyline points="1,3 7,8 13,3"/></svg>
          maren@tartsandtreatsbymaren.example.au
        </li>
        <li class="contact__item">
          <span class="contact__square"></span>
          tartsandtreatsbymaren
        </li>
        <li class="contact__item">
          <span class="contact__square"></span>
          tartsandtreatsbymaren
        </li>
      </ul>
    </div>
    <div class="band">
      <span class="band__seg band__seg--pink"></span>
      <span class="band__seg band__seg--blue"></span>
      <span class="band__seg band__seg--purple"></span>
    </div>
  </section>
</main>
</body>
</html>
```